Tech business card design

We need an amazing business card design for our new business 'Pexla' a marketing tech startup based in Sydney, Australia. We provide an online marketplace for businesses to search and buy advertising media, connect with service providers and learn more about marketing. We wish to communicate 'cool tech', reliability and professionalism and design based around our logo.

Target Market(s)

Business Owners

Contact Information for Business Card

Name
Position
Email Address
Website
Phone Number

Font styles to use
Other font styles liked:
• Avenir & Avenir Next

Colors

Designer to choose colors to be used in the design.

```html
<!DOCTYPE html>
<html lang="en">
<head>
<meta charset="utf-8">
<title>Pexla Business Card</title>
<link href="https://fonts.googleapis.com/css2?family=Nunito+Sans:wght@400;700;800&display=swap" rel="stylesheet">
<style>
  :root {
    --navy: #170f3b;
    --paper: #f4f4f4;
    --backdrop: #e4e4e4;
    --white: #ffffff;
  }
  html, body {
    margin: 0;
    padding: 0;
    width: 1200px;
    height: 960px;
    overflow: hidden;
    background: var(--backdrop);
    font-family: "Nunito Sans", "Avenir Next", Avenir, sans-serif;
  }
  .canvas {
    position: relative;
    width: 1200px;
    height: 960px;
  }
  .card {
    position: absolute;
    left: 335px;
    width: 534px;
    height: 327px;
  }
  .card--front {
    top: 139px;
    background: var(--navy);
    display: flex;
    align-items: center;
    justify-content: center;
  }
  .card--back {
    top: 510px;
    background: var(--paper);
  }
  .wordmark {
    font-weight: 800;
    letter-spacing: -1px;
    line-height: 1;
  }
  .card--front .wordmark {
    color: var(--white);
    font-size: 92px;
    margin-top: -10px;
  }
  .card--back .wordmark {
    position: absolute;
    left: 52px;
    top: 120px;
    color: var(--navy);
    font-size: 68px;
  }
  .divider {
    position: absolute;
    left: 266px;
    top: 108px;
    width: 1.5px;
    height: 109px;
    background: var(--navy);
  }
  .contact {
    position: absolute;
    left: 296px;
    top: 108px;
    color: var(--navy);
  }
  .contact__name {
    margin: 0;
    font-size: 20px;
    font-weight: 800;
    line-height: 24px;
  }
  .contact__role {
    margin: 0 0 16px;
    font-size: 14px;
    font-weight: 400;
    line-height: 18px;
  }
  .contact__list {
    list-style: none;
    margin: 0;
    padding: 0;
    font-size: 14px;
    line-height: 18px;
  }
  .contact__list li {
    display: flex;
    align-items: center;
    gap: 5px;
  }
  .contact__list svg {
    width: 11px;
    height: 11px;
    flex: none;
  }
</style>
</head>
<body>
<div class="canvas">
  <section class="card card--front">
    <span class="wordmark">pexla</span>
  </section>

  <section class="card card--back">
    <span class="wordmark">pexla</span>
    <div class="divider"></div>
    <div class="contact">
      <h1 class="contact__name">Daniel Reeve</h1>
      <p class="contact__role">Founder, Director</p>
      <ul class="contact__list">
        <li>
          <svg viewBox="0 0 12 12" aria-hidden="true"><rect x="3" y="0.7" width="6" height="10.6" rx="1" fill="none" stroke="#170f3b" stroke-width="1.2"/><line x1="5" y1="9.5" x2="7" y2="9.5" stroke="#170f3b" stroke-width="1"/></svg>
          +61 (0)400 555 218
        </li>
        <li>
          <svg viewBox="0 0 12 12" aria-hidden="true"><rect x="0.7" y="2" width="10.6" height="8" fill="none" stroke="#170f3b" stroke-width="1.2"/><polyline points="0.7,2 6,6.5 11.3,2" fill="none" stroke="#170f3b" stroke-width="1.1"/><line x1="0.7" y1="10" x2="4.5" y2="5.5" stroke="#170f3b" stroke-width="1"/><line x1="11.3" y1="10" x2="7.5" y2="5.5" stroke="#170f3b" stroke-width="1"/></svg>
          daniel@pexlamedia.com.au
        </li>
        <li>
          <svg viewBox="0 0 12 12" aria-hidden="true"><circle cx="6" cy="6" r="5.2" fill="none" stroke="#170f3b" stroke-width="1.1"/><ellipse cx="6" cy="6" rx="2.3" ry="5.2" fill="none" stroke="#170f3b" stroke-width="0.9"/><line x1="0.8" y1="6" x2="11.2" y2="6" stroke="#170f3b" stroke-width="0.9"/><line x1="1.6" y1="3.4" x2="10.4" y2="3.4" stroke="#170f3b" stroke-width="0.8"/><line x1="1.6" y1="8.6" x2="10.4" y2="8.6" stroke="#170f3b" stroke-width="0.8"/></svg>
          www.pexlamedia.com.au
        </li>
      </ul>
    </div>
  </section>
</div>
</body>
</html>
```